2021 Summer Ads Hollis Bay Custom Homes

We need a re-design of our summer ad run for our customer, Hollis Bay Custom Homes. They are custom home builders in the mostly rural parts of West Virginia, USA. They are known for their "Forever Home" tagline. We'd like two designed ads with the main difference being just the custom home that's featured. These designs should be for a Zintrola banner like 300 x 250 and square ad like 250 x 250. For inspiration please visit the Hollis Bay Custom Homes website at www dot hollisbaycustomhomes dot com

Target Market(s)

consumers / new home shoppers

Industry/Entity Type

Consumer

Requirements
Must have
• HBCH logo
Price Lock Available!
Custom home pic
Learn more >
small CFRM logo mark

```html
<!DOCTYPE html>
<html lang="en">
<head>
<meta charset="utf-8">
<title>Hollis Bay Custom Homes – Summer Ad</title>
<link rel="stylesheet" href="https://fonts.googleapis.com/css2?family=Anton&family=Cinzel:wght@700&family=Montserrat:wght@600;700;800&display=swap">
<style>
  :root {
    --navy: #1d2230;
    --navy-deep: #141823;
    --red: #e0252e;
    --red-dark: #a9151d;
    --white: #ffffff;
    --sky: #7fb3e0;
    --foliage: #3f6b3a;
    --siding: #e9ecef;
  }
  * { margin: 0; padding: 0; box-sizing: border-box; }
  html, body { width: 1200px; height: 1200px; overflow: hidden; background: var(--navy); }
  .ad {
    position: relative;
    width: 1200px;
    height: 1200px;
    overflow: hidden;
    background: var(--navy);
    font-family: "Montserrat", sans-serif;
    color: var(--white);
  }
  .home-photo {
    position: absolute;
    inset: 0 0 auto 0;
    height: 900px;
    background:
      linear-gradient(160deg, transparent 55%, rgba(63,107,58,.9) 80%),
      linear-gradient(200deg, var(--sky) 0%, #b8d3ea 30%, var(--siding) 55%, #9aa3ab 75%, var(--foliage) 100%);
  }
  .bands { position: absolute; inset: 0; width: 1200px; height: 1200px; }
  .brand {
    position: absolute;
    left: 90px;
    top: 660px;
    width: 450px;
    text-align: center;
  }
  .brand-name {
    font-family: "Cinzel", serif;
    font-weight: 700;
    font-size: 64px;
    line-height: 1;
    letter-spacing: 2px;
    color: var(--white);
  }
  .brand-sub {
    font-family: "Cinzel", serif;
    font-weight: 700;
    font-size: 24px;
    letter-spacing: 6px;
    margin-top: 10px;
    color: var(--white);
  }
  .headline {
    position: absolute;
    left: 75px;
    top: 840px;
    font-family: "Anton", sans-serif;
    font-size: 96px;
    line-height: 94px;
    text-transform: uppercase;
    letter-spacing: 1px;
  }
  .price-lock {
    position: absolute;
    left: 78px;
    top: 1118px;
    font-weight: 700;
    font-size: 42px;
    letter-spacing: 1px;
    text-transform: uppercase;
  }
  .partner {
    position: absolute;
    left: 900px;
    top: 880px;
    width: 210px;
    display: flex;
    align-items: center;
    justify-content: center;
    gap: 14px;
  }
  .partner-square { width: 34px; height: 34px; background: var(--white); }
  .partner-name { font-weight: 800; font-size: 60px; color: var(--white); }
  .cta {
    position: absolute;
    left: 819px;
    top: 1044px;
    width: 336px;
    height: 90px;
    background: var(--red);
    border-radius: 6px;
    display: flex;
    align-items: center;
    justify-content: center;
    font-weight: 700;
    font-size: 30px;
    letter-spacing: 1px;
    text-transform: uppercase;
    color: var(--white);
    text-decoration: none;
  }
</style>
</head>
<body>
  <main class="ad">
    <div class="home-photo" role="img" aria-label="Photo of a white board-and-batten custom home with black roof, cupola, stone base and dark carriage garage doors among green trees"></div>

    <svg class="bands" viewBox="0 0 1200 1200" aria-hidden="true">
      <polygon points="0,230 1200,930 1200,1200 0,1200" fill="var(--navy)"/>
      <polygon points="0,140 1200,840 1200,940 0,240" fill="var(--red)"/>
      <polygon points="0,175 1200,875 1200,895 0,195" fill="var(--red-dark)"/>
      <polygon points="0,215 1200,915 1200,935 0,235" fill="var(--navy-deep)"/>
      <polygon points="640,780 1200,690 1200,740 720,826" fill="var(--red)"/>
    </svg>

    <div class="brand">
      <div class="brand-name">HOLLIS BAY</div>
      <div class="brand-sub">CUSTOM HOMES</div>
    </div>

    <h1 class="headline">Start Building<br>Your Forever<br>Home Today</h1>
    <p class="price-lock">Price Lock Available!</p>

    <div class="partner">
      <span class="partner-square"></span>
      <span class="partner-name">CFRM</span>
    </div>

    <a class="cta" href="#">Learn More</a>
  </main>
</body>
</html>
```